We need a design for a Tequila line that will be infused with cannabis oil.
The design should have at least the following items.

The name Morello Tequila
Marijuana leaf
200 ml fluid
500 mg THC

The lable to be printed will be clear "see through"
The liquid inside the clear bottle will be light gold in color.

Target Market(s)

Marijuana users

Requirements
Must have
• Marijuana leaf
• must say 200 ml
• must say 500 mg thc
Nice to have
• bottle lable will be clear on clear bottle.

```html
<!DOCTYPE html>
<html lang="en">
<head>
<meta charset="utf-8">
<title>Morello Tequila – Label</title>
<link rel="stylesheet" href="https://fonts.googleapis.com/css2?family=Alfa+Slab+One&family=Cinzel:wght@500;600&family=Montserrat:wght@600;700&display=swap">
<style>
  :root {
    --canvas: #f4f4f2;
    --label-fill: #eef5ec;
    --frame-green: #2f5a2c;
    --banner-dark: #1e3a1c;
    --banner-light: #4f6e3a;
    --leaf-green: #3d9b57;
    --band-green: #2f9a58;
    --band-green-dark: #1f7a43;
    --tequila-red: #c5353a;
    --ornament-rose: #e7b7b4;
    --ink-light: #f7f3e4;
    --ink-dark: #2e3a2e;
  }
  html, body {
    margin: 0;
    padding: 0;
    width: 1200px;
    height: 1200px;
    overflow: hidden;
    background: var(--canvas);
  }
  .label-canvas {
    display: block;
    width: 1200px;
    height: 1200px;
  }
  .brand-name {
    font-family: "Alfa Slab One", Georgia, serif;
    fill: var(--ink-light);
  }
  .product-type {
    font-family: "Cinzel", Georgia, serif;
    font-weight: 600;
    fill: var(--ink-light);
    letter-spacing: 2px;
  }
  .volume {
    font-family: "Montserrat", Arial, sans-serif;
    font-weight: 700;
    fill: var(--ink-dark);
  }
  .dose-number {
    font-family: "Cinzel", Georgia, serif;
    font-weight: 500;
    fill: var(--ink-light);
  }
  .dose-unit {
    font-family: "Montserrat", Arial, sans-serif;
    font-weight: 700;
    fill: var(--ink-light);
  }
</style>
</head>
<body>
<svg class="label-canvas" viewBox="130 595 630 630" xmlns="http://www.w3.org/2000/svg">
  <defs>
    <linearGradient id="bannerGradient" x1="0" y1="0" x2="1" y2="1">
      <stop offset="0" stop-color="var(--banner-dark)"/>
      <stop offset="1" stop-color="var(--banner-light)"/>
    </linearGradient>
  </defs>

  <!-- Main label body -->
  <g class="main-label">
    <path class="label-frame"
      d="M305,690 H340 V668 H550 V690 H585 V715 H608 V1055 H585 V1080 H550 V1095 Q445 1122 340 1095 V1080 H305 V1055 H282 V715 H305 Z"
      fill="var(--label-fill)" stroke="var(--frame-green)" stroke-width="7" stroke-linejoin="miter"/>
    <path class="label-frame-inner"
      d="M318,702 H352 V682 H538 V702 H572 V727 H594 V1043 H572 V1068 H538 V1082 Q445 1106 352 1082 V1068 H318 V1043 H296 V727 H318 Z"
      fill="none" stroke="var(--frame-green)" stroke-width="1.6" stroke-dasharray="2 3"/>

    <ellipse class="leaf-illustration" role="img" aria-label="Cannabis leaf illustration"
      cx="445" cy="728" rx="108" ry="82" fill="var(--leaf-green)"/>

    <g class="name-banner">
      <rect x="264" y="790" width="362" height="112" rx="56"
        fill="url(#bannerGradient)" stroke="var(--ink-light)" stroke-width="4"/>
      <rect x="272" y="798" width="346" height="96" rx="48"
        fill="none" stroke="var(--frame-green)" stroke-width="2"/>
      <text class="brand-name" x="445" y="868" text-anchor="middle" font-size="56">MORELLO</text>
    </g>

    <g class="type-box">
      <rect x="346" y="906" width="196" height="48" fill="var(--tequila-red)"
        stroke="var(--ink-light)" stroke-width="3"/>
      <text class="product-type" x="445" y="940" text-anchor="middle" font-size="28">TEQUILA</text>
    </g>

    <rect class="flourish-ornament" role="img" aria-label="Red decorative flourish"
      x="318" y="962" width="254" height="34" rx="17" fill="var(--ornament-rose)"/>

    <g class="volume-ribbon">
      <path d="M358,992 Q445 1040 532 992 L532 1018 Q445 1066 358 1018 Z"
        fill="#ffffff" stroke="var(--band-green)" stroke-width="3"/>
      <text class="volume" x="445" y="1034" text-anchor="middle" font-size="15">200 ML</text>
    </g>
  </g>

  <!-- Dose band -->
  <g class="dose-band">
    <line x1="302" y1="1161" x2="588" y2="1161" stroke="var(--tequila-red)" stroke-width="3"/>
    <line x1="302" y1="1206" x2="588" y2="1206" stroke="var(--tequila-red)" stroke-width="3"/>
    <rect x="284" y="1165" width="320" height="37" rx="8"
      fill="var(--band-green)" stroke="#ffffff" stroke-width="2"/>
    <path class="dose-badge"
      d="M410,1147 H480 Q494 1160 504 1160 V1206 Q494 1206 480 1222 H410 Q396 1206 386 1206 V1160 Q396 1160 410 1147 Z"
      fill="var(--band-green-dark)" stroke="#ffffff" stroke-width="3"/>
    <text class="dose-number" x="445" y="1190" text-anchor="middle" font-size="28">500</text>
    <text class="dose-unit" x="445" y="1206" text-anchor="middle" font-size="10">MG THC</text>
  </g>
</svg>
</body>
</html>
```